Keystonery Billboard - Financial Services Company (Investments, Tax Planning and Insurance)

Our new office has a billboard directly above the office building. We'd like something eye-catching with a strong Call to Action, with the main part of the billboard being under 7 words if possible. We'd like you to include a way to get ahold of us (either our website keystoneryllc.example or our phone number 302-418-2907. You may also include in small font something to indicate that we've been serving the area since 1980 (the DE area, the tri-state area, the Marlowe Hollow, etc.)

We offer financial planning, tax planning, and insurance, and we help our clients to focus on their goals and happiness by providing everything they need for lifelong wealth under one roof.

Our logos are attached, we use a triangle logo with green and gray. We use the tagline "discover lasting prosperity" but this does not need to be included.

Potential ideas we have seen from other financial companies-
- the concept that the driver spends more time looking at billboards than planning for their retirement
-something along the lines of "everything you need for your finances is in this building right here" planning, investments, taxes, insurance"
-don't spend your time worrying about retirement, let us help you plan for it
-are you working for your money, or is it working for you?
- retirement takes planning, we're here to help
- ready to retire? talk to us
- need investment advice?
- need help investing?
- crossing your fingers isn't a retirement plan. we can help.
- retiring soon? you need help.

Those are just general ideas, please feel free to be creative.

brand colors:
#00b585
#00b185
#000000
#ffffff
#6d6f75
#6d6f75
#6f7074
#021712
#052e24

```html
<!DOCTYPE html>
<html lang="en">
<head>
<meta charset="utf-8">
<title>Keystonery Billboard</title>
<link rel="stylesheet" href="https://fonts.googleapis.com/css2?family=Anton&family=Montserrat:wght@500;600;700;800&family=Libre+Baskerville&display=swap">
<style>
  :root {
    --green: #00a566;
    --green-bright: #00b585;
    --ink: #000000;
    --paper: #ffffff;
    --gray: #6d6f75;
    --dark-1: #111111;
    --dark-2: #2c2c2c;
    --backdrop: #c4c4c4;
  }
  * { margin: 0; padding: 0; box-sizing: border-box; }
  html, body { width: 996px; height: 1200px; overflow: hidden; }
  body { background: var(--backdrop); position: relative; font-family: "Montserrat", sans-serif; }

  .billboard {
    position: absolute; left: 28px; top: 463px;
    width: 940px; height: 274px;
    box-shadow: 0 6px 10px rgba(0,0,0,.35);
  }
  .billboard__message {
    position: absolute; left: 0; top: 0; width: 940px; height: 184px;
    background: radial-gradient(ellipse at 55% 45%, var(--dark-2) 0%, var(--dark-1) 75%);
    color: var(--paper);
  }
  .headline {
    position: absolute; top: 16px;
    font-family: "Anton", sans-serif; font-weight: 400;
    font-size: 56px; line-height: 1; letter-spacing: .5px;
  }
  .headline--question { left: 23px; color: var(--paper); }
  .headline--answer { left: 556px; color: var(--green); }

  .offer-tag {
    position: absolute; left: 22px; top: 89px; width: 107px; height: 25px;
    background: var(--green);
    clip-path: polygon(0 0, 86% 0, 100% 100%, 0 100%);
    font-weight: 700; font-size: 17px; line-height: 25px; padding-left: 8px;
  }
  .offer-rule {
    position: absolute; left: 22px; top: 113px; width: 355px; height: 2px; background: var(--green);
  }
  .service {
    position: absolute; top: 124px;
    font-weight: 600; font-size: 19px; line-height: 21px;
    padding-left: 16px;
  }
  .service svg { position: absolute; left: 0; top: 4px; }
  .service--financial { left: 23px; }
  .service--tax { left: 147px; }
  .service--insurance { left: 256px; }

  .region-note {
    position: absolute; left: 565px; top: 94px;
    font-weight: 500; font-size: 16.5px; line-height: 22px;
  }
  .since-badge {
    position: absolute; left: 802px; top: 88px; width: 88px; height: 88px;
    border-radius: 50%; border: 3px solid var(--green);
    background: var(--dark-1);
    box-shadow: inset 0 0 0 3px var(--dark-1), inset 0 0 0 4px var(--paper);
    text-align: center; overflow: hidden;
  }
  .since-badge__top {
    display: block; background: var(--paper); color: var(--ink);
    font-weight: 800; font-size: 12.5px; line-height: 15px; margin-top: 13px;
  }
  .since-badge__mid { display: block; font-weight: 500; font-size: 10px; letter-spacing: 1.5px; line-height: 13px; margin-top: 1px; }
  .since-badge__year { display: block; font-family: "Anton", sans-serif; font-size: 27px; line-height: 30px; }

  .billboard__contact {
    position: absolute; left: 0; top: 184px; width: 940px; height: 90px;
    background: var(--paper);
  }
  .brand {
    position: absolute; left: 23px; top: 14px;
  }
  .brand__mark {
    position: absolute; left: 0; top: 12px; width: 22px; height: 22px; background: var(--green);
  }
  .brand__name {
    position: absolute; left: 32px; top: 0; white-space: nowrap;
    font-family: "Montserrat", sans-serif; font-weight: 600; font-size: 36px; line-height: 46px;
    color: var(--green);
  }
  .brand__tagline {
    position: absolute; left: 33px; top: 46px; white-space: nowrap;
    font-weight: 500; font-size: 8.5px; letter-spacing: 2.6px; text-transform: uppercase; color: var(--gray);
  }
  .contact-divider {
    position: absolute; left: 322px; top: 14px; width: 1px; height: 62px; background: #c8c8c8;
  }
  .phone-icon { position: absolute; left: 342px; top: 19px; }
  .phone-number {
    position: absolute; left: 408px; top: 8px;
    font-weight: 700; font-size: 63px; line-height: 74px; letter-spacing: 1.5px; color: var(--ink);
  }
</style>
</head>
<body>
  <section class="billboard" aria-label="Keystonery billboard">
    <div class="billboard__message">
      <h1 class="headline headline--question">RETIRING SOON?</h1>
      <h2 class="headline headline--answer">YOU NEED HELP</h2>

      <div class="offer-tag">We offer</div>
      <div class="offer-rule"></div>

      <p class="service service--financial">
        <svg width="12" height="12" viewBox="0 0 12 12"><circle cx="6" cy="6" r="6" fill="#00a566"/><path d="M3.2 6.2l1.9 1.8 3.7-3.7" stroke="#111" stroke-width="1.6" fill="none"/></svg>
        Financial<br>planning
      </p>
      <p class="service service--tax">
        <svg width="12" height="12" viewBox="0 0 12 12"><circle cx="6" cy="6" r="6" fill="#00a566"/><path d="M3.2 6.2l1.9 1.8 3.7-3.7" stroke="#111" stroke-width="1.6" fill="none"/></svg>
        Tax<br>planning
      </p>
      <p class="service service--insurance">
        <svg width="12" height="12" viewBox="0 0 12 12"><circle cx="6" cy="6" r="6" fill="#00a566"/><path d="M3.2 6.2l1.9 1.8 3.7-3.7" stroke="#111" stroke-width="1.6" fill="none"/></svg>
        Insurance
      </p>

      <p class="region-note">We've been serving<br>the DE area, tri-state<br>area, Marlowe Hollow</p>

      <div class="since-badge">
        <span class="since-badge__top">SERVING</span>
        <span class="since-badge__mid">SINCE</span>
        <span class="since-badge__year">1980</span>
      </div>
    </div>

    <div class="billboard__contact">
      <div class="brand">
        <span class="brand__mark"></span>
        <span class="brand__name">Keystonery</span>
        <span class="brand__tagline">discover lasting prosperity</span>
      </div>
      <div class="contact-divider"></div>
      <svg class="phone-icon" width="52" height="52" viewBox="0 0 52 52" aria-hidden="true">
        <circle cx="26" cy="26" r="26" fill="#00a566"/>
        <circle cx="26" cy="26" r="19" fill="#ffffff"/>
        <path d="M19 15c1.5-1 2.5-.8 3.3.6l2 3.4c.6 1.1.3 2-.7 2.7l-1.3.9c.9 2.6 2.8 4.7 5.3 6l1-1.2c.8-.9 1.8-1.1 2.8-.4l3.2 2.3c1.2.9 1.3 2 .2 3.3-1.7 2-4 2.6-6.5 1.5-6.1-2.7-10.3-7.4-12.1-13.6-.6-2.3.3-4.3 2.8-5.5z" fill="#00a566"/>
        <path d="M28 16.5a8 8 0 0 1 7.5 7.5M28 12.5a12 12 0 0 1 11.5 11.5" stroke="#00a566" stroke-width="2" fill="none" stroke-linecap="round"/>
      </svg>
      <p class="phone-number">302-418-2907</p>
    </div>
  </section>
</body>
</html>
```